KBT Business Cards

We require business cards for our business. We would like a matte black back to the card, with our logo centred in the middle. The front side of the card is open to design.

Target Market(s)

Clients looking for legal services (professional)

Industry/Entity Type

Legal

Contact Information for Business Card

Doran Kelbrath
Partner
Mobile: 0461 738 524
Email: doran@kbtlaw.co
Website: www.kbtlaw.co
Level 3, 118 Wendmore Street
Sydney NSW 2000

Font styles to use
Other font styles liked:
• Avenir

Colors
f04a50
ffffff
1b1b1b

Requirements
Must have
• Black back with logo included in the centre of the card.
• Our font is Avenir.

```html
<!DOCTYPE html>
<html lang="en">
<head>
<meta charset="utf-8">
<title>KBT Law Business Card</title>
<link href="https://fonts.googleapis.com/css2?family=Roboto:wght@400;500;700&display=swap" rel="stylesheet">
<style>
  :root {
    --red: #d2204a;
    --red-deep: #9a1a36;
    --ink: #1b1b1b;
    --card-black: #231f20;
    --text-grey: #555555;
    --white: #ffffff;
    --backdrop: #e4e4e4;
  }
  * { margin: 0; padding: 0; box-sizing: border-box; }
  html, body {
    width: 1125px; height: 1200px; overflow: hidden;
    background: var(--backdrop);
    font-family: "Roboto", Arial, sans-serif;
  }
  .card {
    position: absolute; left: 171px; width: 826px; height: 471px;
  }
  .card-front { top: 106px; background: var(--white); }
  .card-back { top: 639px; background: var(--card-black); }

  .edge-bar { position: absolute; left: 0; width: 12px; background: var(--ink); }
  .edge-bar.one { top: 106px; height: 56px; }
  .edge-bar.two { top: 194px; height: 69px; }
  .edge-bar.three { top: 287px; height: 74px; }

  .side-accent {
    position: absolute; left: 807px; top: 104px; width: 19px; height: 260px;
    background: linear-gradient(180deg, var(--red), var(--red-deep));
  }

  .holder-name {
    position: absolute; left: 41px; top: 102px;
    font-size: 29px; font-weight: 700; color: var(--red); line-height: 1;
  }
  .holder-role {
    position: absolute; left: 41px; top: 136px;
    font-size: 20px; font-weight: 500; color: var(--ink); line-height: 1;
  }
  .address {
    position: absolute; left: 41px; top: 186px;
    font-size: 19px; line-height: 25px; color: var(--text-grey); font-style: normal;
  }
  .contacts {
    position: absolute; left: 41px; top: 274px; list-style: none;
    font-size: 19px; line-height: 26px; color: var(--text-grey);
  }
  .contacts li { display: flex; align-items: center; gap: 14px; }
  .contacts svg { width: 18px; height: 18px; flex: none; }

  .front-brand {
    position: absolute; left: 520px; top: 206px;
    display: flex; align-items: center; gap: 16px;
  }
  .brand-square { width: 34px; height: 34px; background: var(--red); transform: rotate(45deg); }
  .front-brand .brand-name {
    font-size: 48px; font-weight: 700; color: var(--ink); letter-spacing: 1px; line-height: 1;
  }

  .back-brand {
    position: absolute; left: 0; right: 0; top: 205px;
    display: flex; justify-content: center; align-items: center; gap: 22px;
  }
  .back-brand .brand-square { width: 40px; height: 40px; }
  .back-brand .brand-name {
    font-size: 56px; font-weight: 500; color: var(--white); letter-spacing: 1px; line-height: 1;
  }
  .bottom-band {
    position: absolute; left: 0; bottom: 0; width: 100%; height: 12px;
    background: linear-gradient(90deg, var(--red-deep), var(--red));
  }
</style>
</head>
<body>
  <section class="card card-front">
    <div class="edge-bar one"></div>
    <div class="edge-bar two"></div>
    <div class="edge-bar three"></div>

    <h1 class="holder-name">Doran Kelbrath</h1>
    <p class="holder-role">Partner</p>

    <address class="address">Level 3, 118<br>Wendmore Street<br>Sydney NSW 2000</address>

    <ul class="contacts">
      <li>
        <svg viewBox="0 0 18 18" aria-hidden="true"><rect x="4" y="1" width="10" height="16" rx="1.5" fill="none" stroke="var(--red)" stroke-width="2"/><rect x="7" y="13" width="4" height="1.6" fill="var(--red)"/></svg>
        0461 738 524
      </li>
      <li>
        <svg viewBox="0 0 18 18" aria-hidden="true"><rect x="1" y="4" width="16" height="11" fill="var(--red)"/><path d="M1 4 L9 10 L17 4" fill="none" stroke="#fff" stroke-width="1.4"/></svg>
        doran@kbtlaw.co
      </li>
      <li>
        <svg viewBox="0 0 18 18" aria-hidden="true"><circle cx="9" cy="9" r="8" fill="var(--red)"/><path d="M5 5 q3 1 2 4 q-2 1 -1 4 M11 4 q-1 3 2 4 q2 2 0 4" fill="none" stroke="#fff" stroke-width="1.4"/></svg>
        www.kbtlaw.co
      </li>
    </ul>

    <div class="front-brand">
      <span class="brand-square"></span>
      <span class="brand-name">KBT LAW</span>
    </div>

    <div class="side-accent"></div>
  </section>

  <section class="card card-back">
    <div class="back-brand">
      <span class="brand-square"></span>
      <span class="brand-name">KBT LAW</span>
    </div>
    <div class="bottom-band"></div>
  </section>
</body>
</html>
```